2015 Conference Header

I would like a header designed for our conference next year. It will be used on all of our event promotional material. The information and images that can be used are in the drop box file. I have also included examples of what we have used in the past.

https://www.filecrate.net/sh/7k2m4qwe9zt1pl/BXtRf834pLmnWqYz2cVbH9sDo?dl=0

Industry/Entity Type

Event

Requirements
Must have
• To give you all a little more idea on our branding colours and designs our business website is www.curvellaforms.com

```html
<!DOCTYPE html>
<html lang="en">
<head>
<meta charset="utf-8">
<title>Spinmould 2015 Letterhead</title>
<link href="https://fonts.googleapis.com/css2?family=Roboto+Slab:wght@300;400&display=swap" rel="stylesheet">
<style>
  :root {
    --paper: #ffffff;
    --sky-top: #f6d7b0;
    --sky-glow: #f0b57e;
    --horizon: #c98a63;
    --sea: #6b4636;
    --shore: #3b2720;
    --panel: rgba(20, 14, 12, 0.72);
    --ink-light: #ffffff;
  }
  * { margin: 0; padding: 0; box-sizing: border-box; }
  html, body {
    width: 960px;
    height: 1200px;
    overflow: hidden;
    background: var(--paper);
  }
  .letterhead {
    position: relative;
    width: 960px;
    height: 1200px;
    background: var(--paper);
  }
  .header-band {
    position: absolute;
    top: 0;
    left: 0;
    width: 960px;
    height: 305px;
    overflow: hidden;
  }
  .header-photo {
    position: absolute;
    inset: 0;
    background:
      linear-gradient(90deg, rgba(0,0,0,0) 0%, rgba(0,0,0,0) 45%, rgba(25,16,12,0.55) 70%, rgba(25,16,12,0.7) 100%),
      linear-gradient(180deg,
        var(--sky-top) 0%,
        var(--sky-glow) 28%,
        var(--horizon) 38%,
        var(--sea) 55%,
        var(--shore) 100%);
  }
  .title-panel {
    position: absolute;
    top: 0;
    left: 526px;
    width: 434px;
    height: 179px;
    background: var(--panel);
  }
  .event-details {
    position: absolute;
    top: 0;
    right: 44px;
    text-align: right;
    color: var(--ink-light);
    font-family: 'Roboto Slab', serif;
  }
  .event-title {
    position: absolute;
    right: 0;
    top: 12px;
    white-space: nowrap;
    font-size: 48px;
    font-weight: 400;
    line-height: 1;
  }
  .event-line {
    position: absolute;
    right: 0;
    white-space: nowrap;
    font-size: 21px;
    font-weight: 300;
    line-height: 1;
  }
  .event-location { top: 64px; }
  .event-dates { top: 92px; }
  .event-dates sup { font-size: 11px; vertical-align: 9px; }
  .event-url { top: 124px; font-size: 20px; }
</style>
</head>
<body>
  <main class="letterhead">
    <header class="header-band">
      <div class="header-photo" role="img" aria-label="Photograph: silhouettes of people walking along the shoreline at sunset beside a wooden jetty"></div>
      <div class="title-panel"></div>
      <div class="event-details">
        <h1 class="event-title">Spinmould 2015</h1>
        <p class="event-line event-location">Adelaide, Australia</p>
        <p class="event-line event-dates">21<sup>st</sup>– 23<sup>rd</sup> June</p>
        <p class="event-line event-url">www.spinmouldconference.com.au</p>
      </div>
    </header>
  </main>
</body>
</html>
```